Communication and Marketing agency needs a new presentation card

We are a group of communication and marketing agencies specialized in companies that are in the logistics and industrial sector. The head agency is TELVANO Grupo and the group consists of 4 agencies: TELVANO Media, TELVANO Digital, TELVANO Research and DifundeEnPantalla. We hace 4 offices in Spain (Madrid, Barcelona, Valencia and Murcia). We are looking for a clean and attractive design that transmits our experience, brand presence in the market and knowledge to those who receive the card.It has to maintain the colors of the logo that is attached.
Target Market(s)
logistics and industrial sector
Marketing department
Contact Information for Business Card
Clean and attractive design

```html
<!DOCTYPE html>
<html lang="es">
<head>
<meta charset="utf-8">
<title>TELVANO Grupo – Tarjeta de presentación</title>
<link href="https://fonts.googleapis.com/css2?family=Montserrat:wght@400;500;600;700&display=swap" rel="stylesheet">
<style>
  :root {
    --bg: #1c1c1c;
    --card: #262626;
    --card-edge: #2e2e2e;
    --red: #c8202c;
    --white: #f2f2f2;
    --grey: #bdbdbd;
    --map: #3a3a3a;
  }
  * { margin: 0; padding: 0; box-sizing: border-box; }
  html, body { width: 1200px; height: 900px; overflow: hidden; }
  body {
    background: var(--bg);
    font-family: "Montserrat", sans-serif;
    color: var(--white);
    position: relative;
  }
  .card {
    position: absolute;
    left: 260px;
    width: 680px;
    height: 380px;
    background: linear-gradient(135deg, var(--card-edge), var(--card));
    border-bottom: 7px solid var(--red);
    overflow: hidden;
  }
  .card--front { top: 50px; }
  .card--back { top: 470px; }

  /* Front: agency names grid */
  .agency-grid {
    position: absolute;
    left: 120px; top: 80px;
    width: 460px; height: 210px;
    display: grid;
    grid-template-columns: 1fr 1fr;
    grid-template-rows: 1fr 1fr;
    column-gap: 40px;
    row-gap: 30px;
    align-items: center;
  }
  .agency-name {
    font-weight: 600;
    font-size: 24px;
    letter-spacing: 1px;
    line-height: 1.2;
  }
  .agency-name--red { color: var(--red); }
  .agency-name--white { color: var(--white); }

  /* Back */
  .map-area {
    position: absolute;
    left: 50px; top: 40px;
    width: 300px; height: 230px;
    background: radial-gradient(ellipse at 45% 50%, #4a4a4a, var(--map) 70%, var(--card) 100%);
    border-radius: 30px;
  }
  .offices {
    position: absolute;
    left: 40px; top: 300px;
    font-weight: 600;
    font-size: 17px;
    color: var(--white);
  }
  .divider {
    position: absolute;
    left: 392px; top: 40px;
    width: 3px; height: 300px;
    background: linear-gradient(to bottom, var(--red) 0 45%, var(--white) 45% 100%);
  }
  .contact {
    position: absolute;
    left: 420px; top: 40px;
    width: 240px;
  }
  .brand {
    font-weight: 700;
    font-size: 30px;
    color: var(--red);
    letter-spacing: 1px;
    line-height: 1.1;
  }
  .person-name {
    margin-top: 28px;
    font-weight: 700;
    font-size: 20px;
    color: var(--red);
    letter-spacing: 1px;
  }
  .person-role {
    font-weight: 500;
    font-size: 14px;
    color: var(--white);
    letter-spacing: 1px;
    margin-bottom: 18px;
  }
  .contact-list { list-style: none; }
  .contact-item {
    display: flex;
    align-items: center;
    gap: 10px;
    font-size: 15px;
    font-weight: 500;
    letter-spacing: 0.8px;
    line-height: 1.75;
  }
  .contact-icon { width: 11px; height: 11px; flex: none; }
</style>
</head>
<body>

<section class="card card--front" aria-label="Anverso de la tarjeta">
  <div class="agency-grid">
    <div class="agency-name agency-name--red">TELVANO Media</div>
    <div class="agency-name agency-name--white">TELVANO Research</div>
    <div class="agency-name agency-name--white">TELVANO Digital</div>
    <div class="agency-name agency-name--red">DifundeEnPantalla</div>
  </div>
</section>

<section class="card card--back" aria-label="Reverso de la tarjeta">
  <div class="map-area" role="img" aria-label="Mapa punteado de España con marcadores en Madrid, Barcelona, Valencia y Murcia"></div>
  <p class="offices">Madrid | Barcelona | Valencia | Murcia</p>

  <div class="divider"></div>

  <div class="contact">
    <div class="brand">TELVANO Grupo</div>
    <div class="person-name">Rodrigo Valdés</div>
    <div class="person-role">Director</div>
    <ul class="contact-list">
      <li class="contact-item">
        <svg class="contact-icon" viewBox="0 0 12 12"><path d="M2 1h3l1 3-2 1a7 7 0 0 0 3 3l1-2 3 1v3c-6 0-10-4-10-10z" fill="#c8202c"/></svg>
        910 555 274
      </li>
      <li class="contact-item">
        <svg class="contact-icon" viewBox="0 0 12 12"><rect x="3" y="0.5" width="6" height="11" rx="1" fill="none" stroke="#c8202c" stroke-width="1.3"/></svg>
        600 555 418
      </li>
      <li class="contact-item">
        <svg class="contact-icon" viewBox="0 0 12 12"><rect x="0.7" y="2" width="10.6" height="8" fill="none" stroke="#c8202c" stroke-width="1.2"/><path d="M1 2.5l5 4 5-4" fill="none" stroke="#c8202c" stroke-width="1.2"/></svg>
        rvaldes@telvano.es
      </li>
      <li class="contact-item">
        <svg class="contact-icon" viewBox="0 0 12 12"><circle cx="6" cy="6" r="5" fill="none" stroke="#c8202c" stroke-width="1.2"/><path d="M1 6h10M6 1c-3 3-3 7 0 10M6 1c3 3 3 7 0 10" fill="none" stroke="#c8202c" stroke-width="1"/></svg>
        www.telvano.es
      </li>
      <li class="contact-item">
        <svg class="contact-icon" viewBox="0 0 12 12"><circle cx="6" cy="6" r="5" fill="#c8202c"/></svg>
        rodrigovaldes
      </li>
    </ul>
  </div>
</section>

</body>
</html>
```